New Fun, Positive, energised looking Business Card Needed for High Achiever Coach

I am looking for a two sided full colour business card. I am self employed and have recently re branded my 1-2-1 work re-vitalising high achievers. My target client base for these cards is therefore high achievers - usually aged 40 -55, they are often entrepreneurs, CEO or work in banking and finance and 2/3 are male. I work with them on 90 day or 6 month coaching programs to help them live their success in a healthier, more sustainable and fulfiiled way. They pay for this privately so though they are corporate types the cards need not look 'corporate'. I want to portray the idea of transformation, vitality and re-connecting.
You can get a feel for the look I like on my new website: morvenlisk.co.uk
I want to use this logo with strapline (Re-Vitalising High Achievers) (I purchased off Logoharbor) and font/ colours (the turquoise and green).
Details to include on the card:
www.morvenlisk.co.uk
+44 7915 302618
morven@morvenlisk.co.uk
skype: morvenlisk
I'd also like to include:
Do you struggle to switch off? Want to be healthier and feel fitter? Want closer relationships? More clarity over the direction you are headed? I can help you do these things using integrated mind-body techniques. Visit morvenlisk.co.uk TODAY to apply for a FREE Breakthrough session.
BUT if that is too much text for a card I am open to advice/ammendments.
Updates
Thanks for your design - I am considering them. PLease change the wording to :

```html
<!DOCTYPE html>
<html lang="en">
<head>
<meta charset="utf-8">
<title>Morven Lisk – Business Card</title>
<link rel="stylesheet" href="https://fonts.googleapis.com/css2?family=Open+Sans:wght@400;700&display=swap">
<style>
  :root {
    --turquoise: #1ea9cf;
    --leaf-green: #5fba6b;
    --paper: #ffffff;
    --backdrop: #e9ecee;
    --ink-on-turquoise: #ffffff;
  }
  * { margin: 0; padding: 0; box-sizing: border-box; }
  html, body {
    width: 1200px; height: 720px; overflow: hidden;
    background: var(--backdrop);
    font-family: "Open Sans", Arial, sans-serif;
  }
  .canvas {
    position: relative; width: 1200px; height: 720px;
    display: flex; align-items: center; justify-content: center; gap: 40px;
  }
  .card {
    position: relative; width: 540px; height: 327px; overflow: hidden;
    box-shadow: 0 6px 18px rgba(0,0,0,0.12);
  }
  .card-front { background: var(--paper); }
  .front-shapes { position: absolute; inset: 0; }
  .brand {
    position: absolute; left: 44px; top: 150px;
  }
  .brand-name-row { display: flex; align-items: center; gap: 10px; }
  .brand-dot {
    width: 22px; height: 22px; border-radius: 50%; background: var(--leaf-green);
  }
  .brand-name {
    font-weight: 700; font-size: 34px; color: var(--turquoise); line-height: 1;
  }
  .brand-strapline {
    margin-top: 8px; font-size: 15px; color: var(--turquoise);
  }
  .contact-list {
    position: absolute; left: 355px; top: 48px; list-style: none;
    color: var(--ink-on-turquoise); font-size: 13px;
  }
  .contact-item { display: flex; align-items: center; gap: 7px; height: 22px; }
  .contact-icon { width: 12px; height: 12px; flex: none; }
  .card-back {
    background: var(--turquoise); color: var(--ink-on-turquoise);
    display: flex; flex-direction: column; align-items: center; justify-content: center;
    text-align: center; font-size: 16px; line-height: 1.38; padding: 0 30px;
  }
  .back-questions, .back-offer { margin-bottom: 10px; }
  .back-cta strong { font-weight: 700; }
</style>
</head>
<body>
<main class="canvas">
  <section class="card card-front" aria-label="Business card front">
    <svg class="front-shapes" viewBox="0 0 540 327" width="540" height="327" aria-hidden="true">
      <path d="M236 0 C 330 90 310 250 150 327 L 540 327 L 540 0 Z" fill="var(--leaf-green)"/>
      <path d="M250 0 C 345 90 325 250 166 327 L 540 327 L 540 0 Z" fill="var(--paper)"/>
      <path d="M256 0 C 352 90 332 250 174 327 L 540 327 L 540 0 Z" fill="var(--turquoise)"/>
    </svg>
    <div class="brand">
      <div class="brand-name-row">
        <span class="brand-dot"></span>
        <span class="brand-name">Morven Lisk</span>
      </div>
      <p class="brand-strapline">Re-Vitalising High Achievers</p>
    </div>
    <ul class="contact-list">
      <li class="contact-item">
        <svg class="contact-icon" viewBox="0 0 12 12" aria-hidden="true"><circle cx="6" cy="6" r="5.5" fill="none" stroke="#fff"/><path d="M4 3.5 l1 0 .5 1.3 -.6.5 a3 3 0 0 0 1.8 1.8 l.5-.6 1.3.5 0 1 a1 1 0 0 1-1 .8 A4.5 4.5 0 0 1 3.2 4.5 a1 1 0 0 1 .8-1z" fill="#fff"/></svg>
        <span>+44 7915 302618</span>
      </li>
      <li class="contact-item">
        <svg class="contact-icon" viewBox="0 0 12 12" aria-hidden="true"><rect x="1" y="2.5" width="10" height="7" rx="1" fill="#fff"/><path d="M1.5 3 L6 6.5 L10.5 3" fill="none" stroke="var(--turquoise)"/></svg>
        <span>morven@morvenlisk.co.uk</span>
      </li>
      <li class="contact-item">
        <svg class="contact-icon" viewBox="0 0 12 12" aria-hidden="true"><circle cx="6" cy="6" r="5" fill="none" stroke="#fff"/><ellipse cx="6" cy="6" rx="2.2" ry="5" fill="none" stroke="#fff"/><path d="M1 6 H11" stroke="#fff"/></svg>
        <span>www.morvenlisk.co.uk</span>
      </li>
      <li class="contact-item">
        <svg class="contact-icon" viewBox="0 0 12 12" aria-hidden="true"><circle cx="6" cy="6" r="5.5" fill="#fff"/></svg>
        <span>morvenlisk</span>
      </li>
    </ul>
  </section>

  <section class="card card-back" aria-label="Business card back">
    <p class="back-questions">Do you struggle to switch off?<br>Want to be healthier and feel fitter?<br>Want closer relationships?<br>More clarity over the direction you are headed?</p>
    <p class="back-offer">I can help you do these things using integrated<br>mind-body techniques.</p>
    <p class="back-cta">Visit <strong>morvenlisk.co.uk</strong> TODAY to apply for a<br>FREE Breakthrough session.</p>
  </section>
</main>
</body>
</html>
```